Volbrey Inc Business Card

Looking to get an updated business card for a Contract Machining company (www.volbreyinc.example) - looking for a clean design the portrays the technical nature of the business - colors can follow the website design and be in any combination that makes sense (red black, white, metallic or silver) - logos attached for use also. Would like space for: Name, title, business phone (555 214-3086), cell phone , website (www.volbreyinc.example) - possibly QR code could be integrated for website (designer choice), business address - 418 Harlow Bend, Ashgrove, NR 48199 (cards will be for 4 employees, I will either need to modify a template or I can provide individual information)
Target Market(s)
Aerospace, defense and medical device manufacturing companies that need machining
Industry/Entity Type
Machining for aerospace, defense, medical
Contact Information for Business Card
Name, Title, Business Phone, Cell Phone, email, business website and business address
Look and feel

```html
<!DOCTYPE html>
<html lang="en">
<head>
<meta charset="utf-8">
<title>Volbrey Inc Business Card</title>
<link rel="stylesheet" href="https://fonts.googleapis.com/css2?family=Montserrat:wght@400;500;800&display=swap">
<style>
  :root {
    --stage: #3a3a3a;
    --card-black: #151515;
    --brand-red: #b01f24;
    --paper-white: #ffffff;
    --text-white: #f2f2f2;
  }
  * { box-sizing: border-box; margin: 0; padding: 0; }
  html, body { width: 1200px; height: 900px; overflow: hidden; }
  body {
    background: var(--stage);
    font-family: "Montserrat", sans-serif;
    position: relative;
  }
  .card {
    position: absolute;
    left: 290px;
    width: 620px;
    height: 354px;
    border-radius: 22px;
    background: var(--card-black);
    overflow: hidden;
    box-shadow: 0 10px 28px rgba(0,0,0,0.45);
  }
  .card-back { top: 62px; }
  .card-front { top: 478px; }

  /* back */
  .back-mark {
    position: absolute;
    left: 50%;
    top: 52px;
    width: 160px;
    height: 160px;
    margin-left: -80px;
    border-radius: 50%;
    background: var(--brand-red);
  }
  .back-name {
    position: absolute;
    left: 0; right: 0;
    top: 232px;
    text-align: center;
    color: var(--brand-red);
    font-weight: 800;
    font-size: 40px;
    letter-spacing: 1px;
    white-space: nowrap;
  }

  /* front */
  .front-art { position: absolute; inset: 0; }
  .front-info {
    position: absolute;
    left: 38px;
    top: 36px;
    width: 250px;
    color: var(--text-white);
  }
  .front-name {
    color: var(--brand-red);
    font-weight: 800;
    font-size: 30px;
    letter-spacing: 0.5px;
    line-height: 1;
    white-space: nowrap;
  }
  .person {
    margin-top: 24px;
    padding-left: 16px;
    border-left: 8px solid var(--brand-red);
  }
  .person-name {
    color: var(--brand-red);
    font-weight: 800;
    font-size: 20px;
    letter-spacing: 0.5px;
    line-height: 1.1;
    white-space: nowrap;
  }
  .person-title {
    font-weight: 500;
    font-size: 15px;
    margin-top: 3px;
  }
  .address {
    margin-top: 14px;
    margin-left: 24px;
    font-size: 14px;
    line-height: 1.35;
    font-style: normal;
  }
  .contacts {
    list-style: none;
    margin-top: 12px;
    margin-left: 24px;
    font-size: 14px;
    line-height: 1.4;
  }
  .contacts li { display: flex; align-items: center; gap: 9px; white-space: nowrap; }
  .contacts svg { width: 13px; height: 13px; flex: none; }
</style>
</head>
<body>

  <section class="card card-back" aria-label="Card back">
    <div class="back-mark"></div>
    <div class="back-name">VOLBREY INC.</div>
  </section>

  <section class="card card-front" aria-label="Card front">
    <svg class="front-art" viewBox="0 0 620 354" aria-hidden="true">
      <ellipse cx="515" cy="130" rx="205" ry="190" fill="var(--paper-white)"/>
      <circle cx="510" cy="150" r="135" fill="var(--brand-red)"/>
    </svg>

    <div class="front-info">
      <div class="front-name">VOLBREY INC.</div>

      <div class="person">
        <div class="person-name">DANA WHITFIELD</div>
        <div class="person-title">Managing Director</div>
      </div>

      <address class="address">
        418 Harlow Bend,<br>
        Ashgrove, NR 48199
      </address>

      <ul class="contacts">
        <li>
          <svg viewBox="0 0 16 16"><path fill="var(--brand-red)" d="M3.5 1.5l2.5 3-1.5 1.8c.9 1.9 2.3 3.3 4.2 4.2L10.5 9l3 2.5-1.5 3C6.5 14 2 9.5 1.5 3z"/></svg>
          555 214-3086
        </li>
        <li>
          <svg viewBox="0 0 16 16"><rect x="4" y="1" width="8" height="14" rx="1.5" fill="none" stroke="var(--brand-red)" stroke-width="1.6"/><circle cx="8" cy="12.5" r="0.9" fill="var(--brand-red)"/></svg>
          555-467-9021
        </li>
        <li>
          <svg viewBox="0 0 16 16"><rect x="1" y="3" width="14" height="10" rx="1" fill="var(--brand-red)"/><path d="M1.5 3.5L8 9l6.5-5.5" fill="none" stroke="var(--card-black)" stroke-width="1.3"/></svg>
          info@volbreyinc.example
        </li>
        <li>
          <svg viewBox="0 0 16 16"><circle cx="8" cy="8" r="6.5" fill="var(--brand-red)"/><path d="M1.5 8h13M8 1.5c-3 3.5-3 9.5 0 13M8 1.5c3 3.5 3 9.5 0 13" fill="none" stroke="var(--card-black)" stroke-width="1"/></svg>
          www.volbreyinc.example
        </li>
      </ul>
    </div>
  </section>

</body>
</html>
```